Systems and Technology Consultants - Website

Design & Build a website for a new company which operates in the Systems and Technology space for Transportation, Government and Commercial sectors.

Overall design should be minimalist in nature.
Should also have a feed that provides news and event updates on the main page.
Logo has already been awarded and should be incorporated into the site.

We like the overall layout, functionality and simplicity of the below sites. Submitted designs could be similar to or a combination of the aspects on these sites, or perhaps a whole different concept - we are open to new ideas.
Norvique.com
Teblo.it

Update 1 Dated 27 May 2014

All I am moving away from the Teblo.it website and would like it to be more aligned with Norvique.com not only in layout but in functionality. I will be extending the deadline of this design brief for two weeks to incorporate additional requirements and will add addtional funding to the project.

Apologies for not having more information available to provide but with so many submissions its getting confusing.

Thanks Derek

Please note that the brief has been updated and the deadline has been extended.

Important: We will need two language versions of the website, English and Arabic; the website is hosted on HostPelican

Hello All, Thank you for your submissions. We have narrowed it down to the final 6 designers and I just wanted to take a moment and provide a bit of feedback regarding the concepts that we like and the modifications we are looking for. First, let me mention some of the design functions we like. - At the top of the homepage we really like the "region" or "language" tab so that the website can be viewed in both English and Arabic. - We like the homepage to have clear color variation so that the different sections of the homepage are distinct. Additionally, we like the bottom portion of the homepage to be in red. We feel that draws attention to our contact information. Again, we would like the colors to integrate black, gray-scale, red, etc. - Having a search tab at the top of the home page, or integrated into the main image, so that the site is easy to navigate. - We especially like the main image to have the scrolling tabs at the bottom so it is easy to browse the services offered (Consultancy, Solutions Architecture, Masters Systems Integration, Independent Design Review). - In regards to the services offered tab we really like the idea that a few people presented that have the outside of our logo with an icon in the middle of consultancy, solutions, etc., etc. Secondly, as mentioned in our brief we really enjoy the design of norvique site. Specially, we enjoy the strong iconic images they use, the way the tabs at the top scroll easily, and contact us page that generates an email. Lastly, I've included some photos of the concept we have been working on. What we are trying to demonstrate is how our company offers a range of services that are essentially linked together. We provide individual services that when combined present the full service package. We would like this concept to be integrated into the over concept of our website. Please feel free to ask for clarification of any of the above points or contact us if you have any additional questions. We appreciate all of your hard work and are very excited to see the updated designs. Best, Marta Vennick Quelbrant Senior Program Manager marta.vennick@quelbrant-example.com

Industry/Entity Type

Government

Font styles to use
Serif
Sans Serif

Requirements
Must have
• Must work on/adapt to various/mobile devices (responsive)
Must be simple and straightforward
Colors should be in line/matching with logo
2 language versions: English and Arabic (no Thai)
Services should be the first group/row of items after/below the main image
Note: the website will be hosted by hostpelican
Nice to have
• Submit feedback form
What's New section
The banner at the bottom of the site should not be too large; we would like a narrow one more
It would be nice if the header/top banner (with Home, About, etc. tabs) could stay in place as you scroll down (like Norvique and Chatterloop)
We will likely only use one image with a Company slogan on the Home page rather than a carousel of images to rotate through
Should not have
• This is the existing website: http://www.quelbrant-example.org
We do not like the animation, the way the banner icons/titles bounce
Not simple enough, we don't like the functionality or how pages load so slowly
We do not like the logo centered - it should be at the left
The banner and its tabs should not be towards the right, we would like them to be centered, to go all the way across and to be below the logo

```html
<!DOCTYPE html>
<html lang="en">
<head>
<meta charset="utf-8">
<title>Quelbrant International</title>
<link rel="stylesheet" href="https://fonts.googleapis.com/css2?family=Open+Sans:wght@400;600&family=Roboto:wght@400;500&family=Josefin+Sans:wght@400;600&family=Arimo:wght@400&display=swap">
<style>
:root{
  --red:#d0202a;
  --red-bright:#e5131c;
  --ink:#222;
  --grey:#666;
  --grey-light:#999;
  --rule:#cfcfcf;
  --nav-active:#0f2a35;
  --footer:#333;
  --footer-base:#222;
  --sky-top:#3f8fc0;
  --sky-bottom:#7ec0dd;
}
*{margin:0;padding:0;box-sizing:border-box}
html,body{width:921px;height:1200px;overflow:hidden;background:#fff}
body{position:relative;font-family:"Open Sans",sans-serif;color:var(--ink)}
.abs{position:absolute}

/* header */
.header{left:0;top:0;width:921px;height:120px;background:#fff;border-bottom:2px solid #ddd}
.brand{left:108px;top:34px;display:flex;align-items:center;gap:12px}
.brand-mark{width:26px;height:26px;background:var(--red)}
.brand-name{font-family:"Josefin Sans",sans-serif;font-weight:600;font-size:30px;letter-spacing:6px;color:var(--red);line-height:1}
.brand-sub{font-family:"Josefin Sans",sans-serif;font-weight:600;font-size:10px;letter-spacing:4px;color:var(--red);margin-top:4px}
.lang{left:587px;top:20px;width:41px;height:20px;border:1px solid #ccc;background:#f4f4f4}
.lang span{position:absolute;left:4px;top:4px;width:24px;height:11px;background:#3b4f8f}
.lang i{position:absolute;right:4px;top:8px;border:3px solid transparent;border-top-color:#666}
.phone{left:646px;top:22px;font-family:"Arimo",sans-serif;font-size:15px;color:#222}
.util{left:512px;top:52px;display:flex;font-family:"Arimo",sans-serif;font-size:9.5px;color:var(--grey)}
.util a{color:inherit;text-decoration:none;padding:0 9px;border-left:1px solid #ccc}
.util a:first-child{border-left:0}
.search{left:694px;top:50px;width:112px;height:18px;border:1px solid #bbb;font-family:"Arimo",sans-serif;font-size:11px;color:#888;padding:1px 2px}
.search b{position:absolute;right:0;top:0;width:17px;height:16px;background:#ddd}

/* hero */
.hero{left:0;top:120px;width:921px;height:324px;background:linear-gradient(180deg,var(--sky-top),var(--sky-bottom))}
.hero-photo{left:420px;top:0;width:501px;height:324px;background:linear-gradient(200deg,#1d4e78 0%,#5c8fb5 45%,rgba(200,225,240,.6) 100%)}
.nav{left:99px;top:113px;width:717px;height:40px;background:var(--red);display:flex;font-family:"Arimo",sans-serif;font-size:13px;color:#fff}
.nav a{color:#fff;text-decoration:none;line-height:40px}
.nav .active{background:var(--nav-active);padding:0 24px;margin-left:9px}
.hero-title{left:101px;top:172px;font-family:"Josefin Sans",sans-serif;font-weight:600;font-size:33px;color:#fff}
.hero-text{left:107px;top:232px;font-family:"Josefin Sans",sans-serif;font-size:19.5px;line-height:25px;color:#fff}
.dot{top:339px;width:16px;height:16px;border-radius:50%;background:#4b6f86}
.dot.on{background:#f39a1d}

/* business tabs */
.panel{left:99px;top:379px;width:722px;height:260px;background:#fff}
.tab{top:399px;height:42px;font-size:15px;line-height:44px;text-align:center;background:#eee;border:1px solid #e2e2e2;border-bottom:0}
.tab.on{background:#fff}
.feature{left:108px;top:440px;width:713px;height:173px;background:linear-gradient(90deg,#efefef 0%,#f6f6f6 60%,#fff 100%)}
.feature-art{left:136px;top:475px;width:128px;height:95px;border-radius:40px 48px 30px 30px;background:linear-gradient(180deg,#9a9a9a,#6e6e6e)}
.feature-title{left:293px;top:470px;font-family:"Josefin Sans",sans-serif;font-size:25px;letter-spacing:1.5px;color:var(--red)}
.feature-body{left:296px;top:503px;width:525px;font-family:"Josefin Sans",sans-serif;font-size:13px;line-height:20.2px;color:#333}

/* services */
.service{top:652px;width:202px;border-bottom:2px solid var(--rule);height:79px}
.service h3{font-family:"Roboto",sans-serif;font-weight:500;font-size:14.5px;color:var(--grey)}
.service p{margin-top:12px;font-family:"Roboto",sans-serif;font-size:11px;line-height:14px;color:var(--grey)}
.service svg{position:absolute;right:4px;top:0}
.news-img{top:761px;width:214px;height:118px}
.news-cap{top:890px;width:214px;font-size:12.5px;line-height:19.5px;color:#222}

/* footer */
.footer{left:0;top:954px;width:921px;height:201px;background:var(--footer)}
.footer-brand{left:95px;top:985px;display:flex;align-items:center;gap:12px}
.footer-brand .brand-mark{background:#fff}
.footer-brand .brand-name,.footer-brand .brand-sub{color:#fff}
.footer-brand .brand-name{font-size:22px;letter-spacing:5px}
.footer-brand .brand-sub{font-size:8px;letter-spacing:3px}
.footer-text{left:101px;top:1056px;width:300px;font-size:11.5px;line-height:17.6px;color:#fff}
.footer h4{font-family:"Open Sans",sans-serif;font-weight:400;font-size:14.5px;color:#fff}
.footer-list{left:429px;top:1006px;font-size:11.5px;line-height:17.6px;color:#fff;list-style:none}
.email{left:605px;top:1009px;width:154px;height:31px;background:#fff;font-size:11px;color:#333;padding:8px 6px}
.join{left:759px;top:1009px;width:56px;height:31px;background:var(--red-bright);color:#fff;font-size:12px;font-weight:600;text-align:center;line-height:31px}
.base{left:0;top:1155px;width:921px;height:45px;background:var(--footer-base);text-align:center;font-size:11.5px;line-height:45px;color:#ccc}
</style>
</head>
<body>

<header class="abs header">
  <div class="abs brand">
    <span class="brand-mark"></span>
    <div><div class="brand-name">QUELBRANT</div><div class="brand-sub">INTERNATIONAL</div></div>
  </div>
  <div class="abs lang" aria-label="Language"><span></span><i></i></div>
  <div class="abs phone">Contact Us 555.014.2290</div>
  <nav class="abs util"><a>About Us</a><a>Locations</a><a>Contact Us</a></nav>
  <div class="abs search">Enter Keyword(s)<b></b></div>
</header>

<section class="abs hero">
  <div class="abs hero-photo" role="img" aria-label="Photo of a glass office tower seen from below against a blue sky"></div>
</section>

<nav class="abs nav">
  <a class="active">HOME</a>
  <a style="margin-left:17px">ABOUT US</a>
  <a style="margin-left:47px">BUSINESS UNITS</a>
  <a style="margin-left:47px">SERVICES</a>
  <a style="margin-left:50px">LOCATIONS</a>
  <a style="margin-left:47px">CONTACT US</a>
</nav>

<h1 class="abs hero-title">What will IT leaders focus on in 2014?</h1>
<p class="abs hero-text">Veltarion’ survey shows hiring<br>and spending in key areas. <span style="color:#f39a1d">›</span></p>
<span class="abs dot" style="left:399px"></span>
<span class="abs dot" style="left:435px"></span>
<span class="abs dot" style="left:470px"></span>
<span class="abs dot on" style="left:505px"></span>

<div class="abs panel"></div>
<div class="abs tab on" style="left:108px;width:172px">Quelbrant Consulting</div>
<div class="abs tab" style="left:285px;width:196px">System Energy</div>
<div class="abs tab" style="left:486px;width:183px">Amet Technology</div>

<section class="abs feature"></section>
<div class="abs feature-art" role="img" aria-label="Illustration of a group of people inside a cloud"></div>
<h2 class="abs feature-title">Sitquetamet dolor Ipsum amet</h2>
<p class="abs feature-body">quelbrant specializes in delivering quality professional services and technical projects that support larger business goals.&nbsp; systems are tools that support a greater business function and need. we understand that most t<br>echnical projects are conceptualized to support a larger vision with actual business goals in</p>

<div class="abs service" style="left:123px">
  <h3>IT Staffing Solutions</h3>
  <svg width="20" height="20" viewBox="0 0 20 20"><circle cx="10" cy="10" r="10" fill="#ccc"/><path d="M6 10h7M10 6l4 4-4 4" stroke="#fff" stroke-width="2" fill="none"/></svg>
  <p>Complement and enhance your in-<br>house skills and capabilities</p>
</div>
<div class="abs service" style="left:365px">
  <h3>IT Talent Management</h3>
  <svg width="20" height="20" viewBox="0 0 20 20"><circle cx="10" cy="10" r="10" fill="#ccc"/><path d="M6 10h7M10 6l4 4-4 4" stroke="#fff" stroke-width="2" fill="none"/></svg>
  <p>Optimize how you attract, develop and<br>retain great IT people</p>
</div>
<div class="abs service" style="left:607px">
  <h3>IT Services</h3>
  <svg width="20" height="20" viewBox="0 0 20 20"><circle cx="10" cy="10" r="10" fill="#ccc"/><path d="M6 10h7M10 6l4 4-4 4" stroke="#fff" stroke-width="2" fill="none"/></svg>
  <p>Achieve business goals with managed,<br>project, and outsourced services</p>
</div>

<div class="abs news-img" style="left:117px;background:linear-gradient(160deg,#c9b08a,#8a6a44 60%,#d9d2c3)" role="img" aria-label="Photo of builders studying plans under a timber roof frame"></div>
<div class="abs news-img" style="left:357px;background:linear-gradient(180deg,#6d94c4,#c8d3dd 55%,#6c8a4e)" role="img" aria-label="Photo of a rotating boat lift structure over water"></div>
<div class="abs news-img" style="left:598px;background:linear-gradient(180deg,#7f98b5,#a59a86 55%,#5e5347)" role="img" aria-label="Photo of engineers in hard hats inspecting a site"></div>
<p class="abs news-cap" style="left:119px">Lorem ipsum dolorSit amet consec-<br>teturAdipsicing elit,</p>
<p class="abs news-cap" style="left:359px">Lorem ipsum dolorSit amet consec-<br>teturAdipsicing elit,</p>
<p class="abs news-cap" style="left:600px">Lorem ipsum dolorSit amet consec-<br>teturAdipsicing elit,</p>

<footer class="abs footer"></footer>
<div class="abs footer-brand">
  <span class="brand-mark"></span>
  <div><div class="brand-name">QUELBRANT</div><div class="brand-sub">INTERNATIONAL</div></div>
</div>
<p class="abs footer-text">Lorem ipsum dolorSit amet consecteturAdipsicing elit, ed do euismodTempor incidunt Labore et dolor Magna aliqua.Lorem ipsum dolorSit amet consec-teturAdipsicing elit,</p>
<h4 class="abs" style="left:429px;top:973px">Business Units</h4>
<ul class="abs footer-list">
  <li>Lorem ipsum</li><li>Is simply dummy</li><li>Text of the</li><li>Printing</li><li>And typesrtting</li><li>Industry</li>
</ul>
<h4 class="abs" style="left:608px;top:973px">Join Our Mailing List</h4>
<div class="abs email">Enter your email address...</div>
<div class="abs join">JOIN</div>
<div class="abs base">Copyrights © 2014Quelbrant.com - All Rights Reserved</div>

</body>
</html>
```